Modern Business Card

Modern professional business card with more than just logo and demographic info. Something memorable.

We are a trendy/modern chiropractic group with an emphasis on neurology, hence the minimalist-type brain logo. We want to convey that modern and technical aspect with professionalism and the elite nature of our practice environment.

```html
<!DOCTYPE html>
<html lang="en">
<head>
<meta charset="utf-8">
<title>Vantage Spine – Business Card</title>
<link href="https://fonts.googleapis.com/css2?family=Lato:wght@400;700&display=swap" rel="stylesheet">
<style>
  :root {
    --backdrop: #d4d5d7;
    --paper: #ffffff;
    --band: #66676a;
    --band-dark: #5a5b5e;
    --accent: #4580c6;
    --ink: #2b2b2d;
    --ink-soft: #4a4a4d;
  }
  * { box-sizing: border-box; margin: 0; padding: 0; }
  html, body { width: 1200px; height: 801px; overflow: hidden; }
  body {
    background: var(--backdrop);
    font-family: "Lato", Arial, sans-serif;
    position: relative;
  }
  .card {
    position: absolute;
    width: 560px;
    height: 320px;
    background: var(--paper);
    box-shadow: 0 10px 28px rgba(0,0,0,0.18);
    overflow: hidden;
  }
  .card svg.card-art { position: absolute; inset: 0; }
  .card--front { left: 60px; top: 70px; }
  .card--back { left: 580px; top: 410px; }

  .brand {
    position: absolute;
    display: flex;
    align-items: center;
    gap: 8px;
    color: var(--ink);
    font-weight: 700;
    letter-spacing: 0.05em;
    text-transform: uppercase;
    white-space: nowrap;
  }
  .brand__dot {
    width: 14px; height: 14px;
    border-radius: 50%;
    background: var(--accent);
    flex: none;
  }
  .card--front .brand { left: 44px; top: 150px; font-size: 19px; }
  .card--back .brand { left: 170px; top: 142px; font-size: 34px; gap: 10px; }
  .card--back .brand__dot { width: 22px; height: 22px; }

  .divider {
    position: absolute;
    left: 270px; top: 96px;
    width: 2px; height: 130px;
    background: var(--band);
  }
  .contact {
    position: absolute;
    left: 292px; top: 96px;
    color: var(--ink-soft);
    font-size: 11.5px;
    line-height: 1.5;
  }
  .contact__name { font-size: 17px; color: var(--ink); letter-spacing: 0.01em; white-space: nowrap; }
  .contact__name b { font-weight: 700; }
  .contact__name span { font-weight: 400; }
  .contact__role { font-size: 11.5px; }
  .contact__rule { width: 18px; height: 2px; background: var(--accent); margin: 3px 0 8px; }
  .contact__address { margin-bottom: 6px; }
  .contact__line { display: flex; align-items: center; gap: 8px; }
  .contact__line svg { width: 11px; height: 11px; flex: none; }

  .web-band {
    position: absolute;
    right: 30px; top: 264px;
    color: var(--paper);
    font-size: 17px;
    letter-spacing: 0.02em;
  }
</style>
</head>
<body>

  <section class="card card--front">
    <svg class="card-art" width="560" height="320" viewBox="0 0 560 320" aria-hidden="true">
      <rect x="-260" y="20" width="780" height="270" rx="135" fill="var(--band)"/>
      <rect x="-260" y="46" width="750" height="218" rx="109" fill="var(--paper)"/>
    </svg>

    <div class="brand"><span class="brand__dot"></span>Vantage Spine</div>
    <div class="divider"></div>

    <div class="contact">
      <p class="contact__name"><b>DR. DANA</b> <span>WHITLOW</span></p>
      <p class="contact__role">Chiropractic</p>
      <div class="contact__rule"></div>
      <p class="contact__address">420 Elm Ridge Ave, Dayton,<br>OH 45402, United States</p>
      <p class="contact__line">
        <svg viewBox="0 0 12 12"><rect x="3" y="0.8" width="6" height="10.4" rx="1.2" fill="none" stroke="var(--accent)" stroke-width="1.2"/><circle cx="6" cy="9.3" r="0.7" fill="var(--accent)"/></svg>
        (555) 014-2278
      </p>
      <p class="contact__line">
        <svg viewBox="0 0 12 12"><rect x="0.5" y="2.5" width="11" height="7" fill="var(--accent)"/><path d="M0.5 2.5 L6 6.6 L11.5 2.5" fill="none" stroke="#fff" stroke-width="1"/></svg>
        dana@vantagespine.com
      </p>
      <p class="contact__line">
        <svg viewBox="0 0 12 12"><circle cx="6" cy="6" r="5.2" fill="none" stroke="var(--accent)" stroke-width="1.1"/><ellipse cx="6" cy="6" rx="2.2" ry="5.2" fill="none" stroke="var(--accent)" stroke-width="1"/><line x1="0.8" y1="6" x2="11.2" y2="6" stroke="var(--accent)" stroke-width="1"/></svg>
        www.vantagespine.com
      </p>
    </div>
  </section>

  <section class="card card--back">
    <svg class="card-art" width="560" height="320" viewBox="0 0 560 320" aria-hidden="true">
      <path d="M0 120 L0 320 L330 320 Z" fill="var(--accent)"/>
      <rect x="24" y="26" width="760" height="300" rx="150" fill="var(--paper)"/>
      <rect x="0" y="18" width="560" height="22" fill="var(--band-dark)"/>
      <rect x="52" y="40" width="760" height="256" rx="128" fill="var(--band-dark)"/>
      <rect x="76" y="60" width="760" height="200" rx="100" fill="var(--paper)"/>
    </svg>

    <div class="brand"><span class="brand__dot"></span>Vantage Spine</div>
    <p class="web-band">www.vantagespine.com</p>
  </section>

</body>
</html>
```